Professional Engineering Web Design

Project Brief: Website Redesign for Mechanical Design Consultancy
Project Overview
I want to update and improve my current website to create a more professional, modern, and high-credibility online presence for my mechanical design consultancy.

Current site: https://valtorix.design/

The new website must communicate expertise, precision, and trust—matching the standard of top engineering and product design agencies.

Reference Websites (Style + Structure Inspiration)
These represent the quality, cleanliness, and professionalism I want to achieve:

https://plinthwaredesign.com/
https://www.sorvane.com/
https://bramlow-uk.com/
Brand Look
Professional, modern, engineering-focused aesthetic
Clean layouts and strong typography
High-quality imagery conveying precision, innovation, and mechanical expertise
Colour scheme and styling must follow my existing logo (attached in project)
Platform Requirements
The website must be built on WordPress
Should use a clean, flexible theme or modern page builder (Elementor, Gutenberg, Bricks, or similar)
Avoid overly complex custom coding so I can easily edit content later
Final deliverable must allow me to manage and update content without developer assistance
Functionality
Fast-loading, lightweight, and smooth user experience
Clean animations and transitions similar to the reference sites
Fully mobile responsive
Clear navigation and strong visual hierarchy
Contact forms optimised for lead generation
Optional: subtle scroll effects, case study sliders, icon animations, etc.
SEO Aspirations
Developer should recommend and implement a modern SEO strategy
Proper on-page SEO setup (titles, meta, schema, alt tags, heading structure)
Optimised site architecture for ranking and crawling
Aim: Generate leads through improved visibility and keyword targeting
Optional but useful: Google Analytics, Google Search Console setup
User Journeys
(Recommended structure)

The site should be crafted around clear, intuitive journeys for each type of visitor:

Potential new clients
Quickly understand what services I offer
View examples of past work / case studies
See credibility indicators (process, expertise, industries served)
Easily contact me or request a project discussion
Returning clients
Access updated portfolio items
Find contact details or book follow-up work easily
General visitors discovering through SEO
Be guided to core service areas
Understand my value proposition quickly
Be invited to learn more or make contact
The developer should design the structure to support these journeys smoothly.

Maintenance Expectations
Website will be maintained by me, so it should be easy to update using relatively basic WordPress skills
Use modular templates and simple backend structure
Avoid unnecessary plugins
Provide brief handover documentation if required
Hosting Preferences
Site is currently hosted via a family member
Open to discussing moving to a paid, reliable hosting provider if preferable for performance and maintainability
Developer may advise on the best hosting setup for WordPress
Content
Most content can be taken from the existing website
Developer is welcome to suggest improvements to structure, layout, and imagery
Must remain easy for me to edit or add new content later (e.g., new projects)
Deliverables
Fully built WordPress website
Clean, professional, modern design inspired by the reference sites
Mobile-responsive across all devices
SEO-ready structure and optimisations
Transfer of website and admin rights
Any design assets, templates, or documentation used

```html
<!DOCTYPE html>
<html lang="en">
<head>
<meta charset="utf-8">
<title>Valtorix Mechanical Design</title>
<link href="https://fonts.googleapis.com/css2?family=Montserrat:wght@500;600;700&family=Lato:ital,wght@0,400;0,700;1,400&display=swap" rel="stylesheet">
<style>
:root{
  --blue:#2540e8;
  --blue-dark:#1c32c9;
  --ink:#333333;
  --dark:#3b3b3b;
  --muted:#444;
  --white:#ffffff;
}
*{box-sizing:border-box;margin:0;padding:0}
html,body{width:1200px;height:4454px;overflow:hidden}
body{position:relative;background:var(--white);font-family:'Lato',sans-serif;color:var(--ink)}
.abs{position:absolute}
h1,h2,h3,h4{font-family:'Montserrat',sans-serif;font-weight:600}
.btn{position:absolute;display:flex;align-items:center;justify-content:center;background:var(--blue);color:var(--white);font-family:'Lato',sans-serif;font-weight:700;border-radius:24px;text-decoration:none;font-size:15px}
.divider{position:absolute;width:84px;height:10px}
.divider::before,.divider::after{content:"";position:absolute;top:4px;width:34px;height:3px;background:var(--blue)}
.divider::before{left:0}.divider::after{right:0}
.divider span{position:absolute;left:37px;top:0;width:10px;height:10px;border-radius:50%;background:var(--blue)}
.divider.light::before,.divider.light::after,.divider.light span{background:var(--white)}
.center{text-align:center}
.arrow{position:absolute;width:34px;height:34px;border-radius:50%;display:flex;align-items:center;justify-content:center}
/* header */
.site-header{position:absolute;left:0;top:0;width:1200px;height:104px;background:var(--white)}
.brand{position:absolute;left:112px;top:22px;display:flex;align-items:center;gap:14px}
.brand-dot{width:58px;height:58px;border-radius:50%;background:var(--blue)}
.brand-name{font-family:'Montserrat',sans-serif;font-weight:600;font-size:38px;color:var(--blue);letter-spacing:1px}
.main-nav a{position:absolute;top:41px;font-size:15px;color:var(--ink);text-decoration:none}
.main-nav a.active{color:var(--blue);text-decoration:underline}
/* hero */
.hero-photo{position:absolute;left:0;top:104px;width:1200px;height:660px;background:linear-gradient(100deg,#6b625a 0%,#3e3935 35%,#2b2826 60%,#4b4540 100%)}
.hero-title{position:absolute;left:584px;top:212px;font-size:45px;line-height:60px;color:var(--white);font-weight:700}
.hero-text{position:absolute;left:584px;top:350px;width:505px;font-size:20px;line-height:29px;color:var(--white);text-align:justify}
/* work */
.section-title{position:absolute;left:0;width:1200px;text-align:center;font-size:40px;color:var(--ink)}
.section-lead{position:absolute;left:0;width:1200px;text-align:center;font-size:16px;line-height:26px;color:var(--muted)}
.work-img{position:absolute;width:277px;height:277px;border-radius:50%}
.work-title{position:absolute;width:330px;text-align:center;font-size:23px;color:var(--ink)}
.work-text{position:absolute;width:300px;text-align:center;font-size:14px;line-height:24px;color:var(--muted)}
/* about + services */
.about-title{position:absolute;left:493px;top:1708px;font-size:42px;color:var(--white)}
.about-text{position:absolute;left:493px;top:1795px;width:480px;font-size:15.5px;line-height:25.5px;color:var(--white);text-align:justify}
.svc-img{position:absolute;width:187px;height:187px;border-radius:50%}
.svc-icon{position:absolute;width:90px;height:90px;border-radius:50%;background:var(--white);border:2px solid var(--blue);display:flex;align-items:center;justify-content:center}
.svc-title{position:absolute;width:240px;text-align:center;font-size:20px;color:var(--white);font-weight:700}
.svc-text{position:absolute;width:240px;text-align:center;font-size:14px;line-height:21px;color:var(--white)}
/* testimonials */
.quote{position:absolute;left:112px;top:2950px;width:500px;font-size:16.5px;line-height:27.5px;font-style:italic;color:var(--muted)}
.client-name{position:absolute;left:112px;top:3100px;font-size:20px;color:var(--blue);font-weight:700;font-family:'Lato',sans-serif}
.client-role{position:absolute;left:112px;top:3132px;font-size:16px;color:var(--muted)}
.client-photo{position:absolute;border-radius:50%;background:radial-gradient(circle at 50% 40%,#8a8f96,#3d434a)}
/* expertise */
.exp-icon{position:absolute;width:110px;height:110px}
.exp-title{position:absolute;width:280px;text-align:center;font-size:21px;line-height:29px;color:var(--ink);font-weight:500}
.exp-text{position:absolute;width:240px;text-align:center;font-size:14px;line-height:22px;color:var(--muted)}
/* footer */
.footer-head{position:absolute;top:4093px;font-size:20px;color:var(--white);font-family:'Montserrat',sans-serif;font-weight:500}
.footer-text{position:absolute;left:111px;top:4150px;width:240px;font-size:14px;line-height:25px;color:var(--white)}
.footer-links a{position:absolute;font-size:14px;color:var(--white);text-decoration:none}
.contact-row{position:absolute;left:650px;display:flex;gap:22px;font-size:14px;line-height:22px;color:var(--white)}
.footer-rule{position:absolute;left:111px;top:4400px;width:978px;height:1px;background:#555}
.copyright{position:absolute;left:0;top:4418px;width:1200px;text-align:center;font-size:12px;color:var(--white)}
</style>
</head>
<body>

<header class="site-header">
  <div class="brand"><span class="brand-dot"></span><span class="brand-name">Valtorix</span></div>
  <nav class="main-nav">
    <a class="active" style="left:479px">Home</a>
    <a style="left:559px">Portfolio</a>
    <a style="left:658px">Our Services</a>
    <a style="left:783px">Contact Us</a>
  </nav>
  <a class="btn" style="left:899px;top:29px;width:189px;height:44px">Start Your Project</a>
</header>

<section class="hero">
  <div class="hero-photo" role="img" aria-label="Engineer holding a precision mechanical component at his workbench"></div>
  <svg class="abs" style="left:0;top:640px" width="1200" height="160" viewBox="0 0 1200 160">
    <path d="M0 30 Q600 170 1200 30 L1200 160 L0 160 Z" fill="#fff"/>
    <path d="M80 55 Q600 150 1125 50 Q600 130 80 55 Z" fill="var(--blue)"/>
    <rect x="566" y="100" width="66" height="40" fill="#fff"/>
    <rect x="576" y="110" width="45" height="23" fill="var(--dark)"/>
  </svg>
  <h1 class="hero-title">We Engineer Products<br>That Perform</h1>
  <p class="hero-text">Specializing in mechanical design, CAD development, and engineered solutions for innovators and industry leaders.</p>
  <a class="btn" style="left:584px;top:470px;width:189px;height:42px">Start Your Project</a>
</section>

<section class="our-work">
  <h2 class="section-title" style="top:870px">Our Work</h2>
  <div class="divider" style="left:558px;top:925px"><span></span></div>
  <p class="section-lead" style="top:958px">Real project outcomes showcasing our mechanical design expertise, CAD development,<br>and end-to-end technical delivery.</p>

  <div class="arrow" style="left:56px;top:1167px;background:var(--blue)"><svg width="14" height="14" viewBox="0 0 14 14"><path d="M9 2 L4 7 L9 12" stroke="#fff" stroke-width="2.4" fill="none"/></svg></div>
  <div class="arrow" style="left:1109px;top:1167px;background:var(--blue)"><svg width="14" height="14" viewBox="0 0 14 14"><path d="M5 2 L10 7 L5 12" stroke="#fff" stroke-width="2.4" fill="none"/></svg></div>

  <div class="work-img" style="left:111px;top:1039px;background:radial-gradient(circle at 50% 60%,#c9c9cb,#6e5f55 70%)" role="img" aria-label="Classic silver car fitted with custom three-piece alloy wheels"></div>
  <div class="work-img" style="left:461px;top:1039px;background:radial-gradient(circle at 50% 55%,#4b5a44,#1d1f1d 70%)" role="img" aria-label="Racing driver in a green go-kart on track"></div>
  <div class="work-img" style="left:811px;top:1039px;background:radial-gradient(circle at 50% 40%,#9fa9b9,#4b5568 75%)" role="img" aria-label="Row of colourful electrical switchgear insulators"></div>

  <h3 class="work-title" style="left:84px;top:1334px">3-Piece Alloy Wheels</h3>
  <h3 class="work-title" style="left:433px;top:1334px">Go-Kart Simulator Design</h3>
  <h3 class="work-title" style="left:784px;top:1334px">Electrical Switchgear</h3>
  <p class="work-text" style="left:99px;top:1380px">We have been working on a long term project to bring custom 3-piece Japanese style wheels to market since 2020.</p>
  <p class="work-text" style="left:448px;top:1380px">Our client already had an existing product, but wanted it updating and refreshing to offer their customers a better product.</p>
  <p class="work-text" style="left:799px;top:1380px">In the UK a lot of electrical switchgear in grid sub-stations are very old, many of them originating in the 60s.</p>
  <a class="btn" style="left:172px;top:1471px;width:155px;height:42px">Read More</a>
  <a class="btn" style="left:522px;top:1471px;width:155px;height:42px">Read More</a>
  <a class="btn" style="left:872px;top:1471px;width:155px;height:42px">Read More</a>
</section>

<section class="about-services">
  <svg class="abs" style="left:0;top:1600px" width="1200" height="1114" viewBox="0 0 1200 1114">
    <defs>
      <linearGradient id="aboutShade" x1="0" y1="0" x2="1" y2="0">
        <stop offset="0" stop-color="#2f2f2f"/><stop offset="0.6" stop-color="#474747"/><stop offset="1" stop-color="#3a3a3a"/>
      </linearGradient>
      <linearGradient id="portraitTone" x1="0" y1="0" x2="0" y2="1">
        <stop offset="0" stop-color="#8c7466"/><stop offset="1" stop-color="#3f4652"/>
      </linearGradient>
    </defs>
    <path d="M0 330 C180 120 480 42 760 42 C950 42 1120 80 1200 110 L1200 1114 L0 1114 Z" fill="url(#aboutShade)"/>
    <g role="img" aria-label="Portrait of the chief engineer">
      <path d="M150 40 Q280 0 400 40 L450 560 L0 560 L0 400 Q60 300 150 40 Z" fill="url(#portraitTone)"/>
    </g>
    <path d="M0 560 C150 440 400 400 620 400 C880 400 1100 540 1200 790 L1200 1114 L0 1114 Z" fill="var(--blue)"/>
  </svg>

  <h2 class="about-title">About Us</h2>
  <div class="divider light" style="left:493px;top:1765px"><span></span></div>
  <p class="about-text">Elliot Marsh is the Chief Engineer at Valtorix Mechanical Design. He has 11 years experience working as a mechanical design engineer in multiple industries including high performance automotive, consumer products, medical, industrial plus many more. He has worked in multiple roles across a wide range of products.</p>
  <a class="btn" style="left:818px;top:1964px;width:155px;height:40px">Read More</a>

  <h2 class="section-title" style="top:2117px;color:var(--white);font-size:42px">Our Services</h2>
  <div class="divider light" style="left:558px;top:2173px"><span></span></div>
  <p class="section-lead" style="top:2205px;color:var(--white)">Mechanical engineering and product development services designed to deliver reliable,<br>high-performance results from concept to production.</p>

  <div class="arrow" style="left:59px;top:2391px;background:var(--white)"><svg width="14" height="14" viewBox="0 0 14 14"><path d="M9 2 L4 7 L9 12" stroke="var(--blue)" stroke-width="2.4" fill="none"/></svg></div>
  <div class="arrow" style="left:1112px;top:2391px;background:var(--white)"><svg width="14" height="14" viewBox="0 0 14 14"><path d="M5 2 L10 7 L5 12" stroke="var(--blue)" stroke-width="2.4" fill="none"/></svg></div>

  <div class="svc-img" style="left:122px;top:2306px;background:radial-gradient(circle at 50% 45%,#b48a55,#3a342f 75%)" role="img" aria-label="Engineer inspecting a machined part"></div>
  <div class="svc-img" style="left:380px;top:2306px;background:radial-gradient(circle at 50% 45%,#6d7a72,#2c302e 75%)" role="img" aria-label="Design team working at CAD workstations"></div>
  <div class="svc-img" style="left:639px;top:2306px;background:radial-gradient(circle at 50% 55%,#3d7fe0,#1b2330 75%)" role="img" aria-label="Blue part being produced on a 3D printer"></div>
  <div class="svc-img" style="left:898px;top:2306px;background:radial-gradient(circle at 50% 45%,#9aa3ad,#44505c 75%)" role="img" aria-label="Project team meeting around a laptop"></div>

  <div class="svc-icon" style="left:131px;top:2441px"><svg width="44" height="44" viewBox="0 0 44 44" fill="none" stroke="var(--blue)" stroke-width="2"><rect x="6" y="8" width="32" height="28"/><circle cx="18" cy="22" r="6"/><path d="M28 14 L34 30 M10 32 L22 32"/></svg></div>
  <div class="svc-icon" style="left:389px;top:2441px"><svg width="44" height="44" viewBox="0 0 44 44" fill="none" stroke="var(--blue)" stroke-width="2"><path d="M22 10 a9 9 0 0 1 5 16 v4 h-10 v-4 a9 9 0 0 1 5 -16 Z"/><path d="M18 34 h8 M22 2 v4 M8 16 h-4 M40 16 h-4 M11 7 l3 3 M33 7 l-3 3"/></svg></div>
  <div class="svc-icon" style="left:648px;top:2441px"><svg width="44" height="44" viewBox="0 0 44 44" fill="none" stroke="var(--blue)" stroke-width="2"><rect x="6" y="6" width="32" height="8"/><path d="M10 14 v24 M34 14 v24 M6 38 h32"/><rect x="18" y="16" width="8" height="6"/><path d="M22 22 v6 M17 32 h10"/></svg></div>
  <div class="svc-icon" style="left:907px;top:2441px"><svg width="44" height="44" viewBox="0 0 44 44" fill="none" stroke="var(--blue)" stroke-width="2"><rect x="14" y="6" width="26" height="22"/><path d="M20 22 v-6 M26 22 v-10 M32 22 v-4"/><circle cx="13" cy="30" r="7"/><circle cx="13" cy="30" r="2.5"/></svg></div>

  <h3 class="svc-title" style="left:96px;top:2549px">Mechanical Design</h3>
  <h3 class="svc-title" style="left:354px;top:2549px">Design Consultancy</h3>
  <h3 class="svc-title" style="left:613px;top:2549px">3D Printing</h3>
  <h3 class="svc-title" style="left:872px;top:2549px">Project Management</h3>
  <p class="svc-text" style="left:96px;top:2582px">Our primary service is<br>mechanical design from initial</p>
  <p class="svc-text" style="left:354px;top:2582px">If you've got a great idea and<br>want to begin developing</p>
  <p class="svc-text" style="left:613px;top:2582px">We have worked on hundreds<br>of projects over the</p>
  <p class="svc-text" style="left:872px;top:2582px">We specialise in Design for<br>Manufacture (DFM).</p>
</section>

<section class="testimonials">
  <h2 class="abs" style="left:112px;top:2840px;font-size:42px;color:var(--ink)">What Our Clients Say</h2>
  <div class="divider" style="left:112px;top:2903px"><span></span></div>
  <p class="quote">"Elliot's description of his abilities was accurate. He is very capable and responsive. He worked very quickly and efficiently, cheerfully incorporating suggestions and revisions within a short time frame. I have no hesitation in recommending Elliot to anyone who needs mechanical engineering work, or calculations, done."</p>
  <p class="client-name">Rowan Hadley</p>
  <p class="client-role">Client</p>
  <div class="arrow" style="left:113px;top:3173px;background:var(--dark)"><svg width="14" height="14" viewBox="0 0 14 14"><path d="M9 2 L4 7 L9 12" stroke="#fff" stroke-width="2.4" fill="none"/></svg></div>
  <div class="arrow" style="left:156px;top:3173px;background:var(--dark)"><svg width="14" height="14" viewBox="0 0 14 14"><path d="M5 2 L10 7 L5 12" stroke="#fff" stroke-width="2.4" fill="none"/></svg></div>

  <div class="client-photo" style="left:914px;top:2818px;width:156px;height:156px" role="img" aria-label="Client portrait"></div>
  <div class="client-photo" style="left:717px;top:2918px;width:94px;height:94px" role="img" aria-label="Client portrait"></div>
  <div class="client-photo" style="left:851px;top:3005px;width:66px;height:66px" role="img" aria-label="Client portrait"></div>
  <div class="client-photo" style="left:980px;top:3052px;width:104px;height:104px" role="img" aria-label="Client portrait"></div>
  <div class="client-photo" style="left:774px;top:3122px;width:122px;height:122px" role="img" aria-label="Client portrait"></div>
</section>

<section class="expertise">
  <h2 class="section-title" style="top:3327px;font-size:42px">Our Expertise</h2>
  <div class="divider" style="left:558px;top:3384px"><span></span></div>
  <p class="section-lead" style="top:3416px">We are a UK based design consultancy offering a comprehensive mechanical and product<br>design service from initial concepts through to full volume production.</p>

  <svg class="abs" style="left:0;top:3480px" width="1200" height="200" viewBox="0 0 1200 200" fill="none">
    <path d="M275 50 C400 20 500 30 555 110" stroke="#555" stroke-width="1.5" stroke-dasharray="6 5"/>
    <path d="M655 140 C760 180 900 150 955 95" stroke="#555" stroke-width="1.5" stroke-dasharray="6 5"/>
  </svg>

  <svg class="exp-icon" style="left:161px;top:3489px" viewBox="0 0 110 110"><circle cx="55" cy="55" r="55" fill="var(--blue)"/><circle cx="55" cy="55" r="33" fill="none" stroke="#fff" stroke-width="3"/><rect x="42" y="44" width="26" height="22" fill="none" stroke="#fff" stroke-width="2.5"/><circle cx="52" cy="55" r="5" fill="none" stroke="#fff" stroke-width="2"/></svg>
  <svg class="exp-icon" style="left:545px;top:3567px" viewBox="0 0 110 110"><circle cx="55" cy="55" r="55" fill="var(--blue)"/><circle cx="55" cy="55" r="33" fill="none" stroke="#fff" stroke-width="3"/><path d="M55 38 L70 46 L70 64 L55 72 L40 64 L40 46 Z M40 46 L55 54 L70 46 M55 54 L55 72" fill="none" stroke="#fff" stroke-width="2.5"/></svg>
  <svg class="exp-icon" style="left:929px;top:3489px" viewBox="0 0 110 110"><circle cx="55" cy="55" r="55" fill="var(--blue)"/><circle cx="55" cy="55" r="33" fill="none" stroke="#fff" stroke-width="3"/><path d="M40 68 V50 L48 56 V50 L56 56 V42 H64 V68 Z" fill="none" stroke="#fff" stroke-width="2.5"/></svg>

  <h3 class="exp-title" style="left:76px;top:3619px">Bespoke Product<br>Design</h3>
  <p class="exp-text" style="left:96px;top:3681px">Innovative design from concept through the full development life cycle</p>
  <h3 class="exp-title" style="left:460px;top:3696px">3D Modelling and<br>Drawings</h3>
  <p class="exp-text" style="left:480px;top:3759px">We create 3D CAD, 2D engineering drawings and photorealistic renders</p>
  <h3 class="exp-title" style="left:844px;top:3619px">Design<br>for Manufacture</h3>
  <p class="exp-text" style="left:864px;top:3681px">Creating designs optimised for prototype and production manufacture</p>
</section>

<footer class="site-footer">
  <svg class="abs" style="left:0;top:3930px" width="1200" height="524" viewBox="0 0 1200 524">
    <path d="M0 118 Q600 -40 1200 118 L1200 524 L0 524 Z" fill="var(--dark)"/>
    <path d="M80 112 Q600 -50 1125 92 Q600 -10 80 112 Z" fill="var(--blue)"/>
    <rect x="566" y="0" width="66" height="40" fill="#fff"/>
    <rect x="576" y="14" width="45" height="20" fill="var(--dark)"/>
  </svg>

  <h4 class="footer-head" style="left:111px">Curious what else we do?</h4>
  <p class="footer-text">Explore more of our mechanical design and engineering capabilitie. See how else we support your product development.</p>
  <a class="btn" style="left:111px;top:4279px;width:154px;height:40px">See Here</a>

  <h4 class="footer-head" style="left:432px">Main Links</h4>
  <nav class="footer-links">
    <a style="left:434px;top:4146px">Home</a>
    <a style="left:434px;top:4186px">Portfolio</a>
    <a style="left:434px;top:4227px">Our Services</a>
    <a style="left:434px;top:4267px">Testimonial</a>
    <a style="left:434px;top:4308px">Contact Us</a>
  </nav>

  <h4 class="footer-head" style="left:650px">Contact Us</h4>
  <div class="contact-row" style="top:4146px"><svg width="18" height="20" viewBox="0 0 18 20" fill="none" stroke="#fff" stroke-width="1.5"><path d="M9 19 C4 13 2 10 2 7 a7 7 0 0 1 14 0 c0 3 -2 6 -7 12 Z"/><circle cx="9" cy="7" r="2.5"/></svg><span>We're based in South<br>Wales, UK.</span></div>
  <div class="contact-row" style="top:4241px"><svg width="18" height="18" viewBox="0 0 18 18" fill="none" stroke="#fff" stroke-width="1.5"><path d="M3 1.5 h3.5 l1.5 4 -2 1.5 a10 10 0 0 0 5 5 l1.5 -2 4 1.5 v3.5 a1.5 1.5 0 0 1 -1.5 1.5 A15 15 0 0 1 1.5 3 A1.5 1.5 0 0 1 3 1.5 Z"/></svg><span>+44 (0)7700 900 314</span></div>
  <div class="contact-row" style="top:4308px"><svg width="18" height="16" viewBox="0 0 18 16" fill="none" stroke="#fff" stroke-width="1.5"><rect x="1" y="2" width="16" height="12"/><path d="M1 2 L9 9 L17 2"/></svg><span>info@valtorix.design</span></div>

  <h4 class="footer-head" style="left:956px">Other Links</h4>
  <nav class="footer-links">
    <a style="left:956px;top:4146px">Contact U</a>
    <a style="left:956px;top:4186px">Privacy Policy</a>
    <a style="left:956px;top:4227px">Terms &amp; Conditions</a>
    <a style="left:956px;top:4267px">Cookies Policy</a>
    <a style="left:956px;top:4308px">Careers</a>
  </nav>

  <div class="footer-rule"></div>
  <p class="copyright">Copyright © 2025 Valtorix Mechanical Design. All rights reserved.</p>
</footer>

</body>
</html>
```